Bespoke Builders Business Card Design

We need a business card for an established builder of high quality bespoke homes in Auckland and Northland. We build and renovate homes collaboratively facilitating effective communication between owners, builders, architects, suppliers and tradespeople. We have never built or renovated a home that leaks or has faults. We only use reliable materials. We have never been sued or had legal action taken against us. We are honest builders of bespoke homes not group mass produced homes. Our niche market is in character homes. We practice sustainability and have built a lot of coastal property. We have been in business for over thirty years . We would like to see natural colors of the environment sand,sea and maybe vegetation . The design should communicate quality, sustainability,fair pricing, open communication and the originality of bespoke building. And the fact that the builder is registered.

Industry/Entity Type

Business

Contact Information for Business Card

Rowan Tellick Builders
Ph. 021583917
18 Kestrel Rd Harwood Bay Auckland 0814
PO Box 927 Mangawhai 0583

```html
<!DOCTYPE html>
<html lang="en">
<head>
<meta charset="utf-8">
<title>Rowan Tellick Builders — Business Card</title>
<link rel="stylesheet" href="https://fonts.googleapis.com/css2?family=Libre+Bodoni:wght@400;700&family=PT+Sans:wght@400&display=swap">
<style>
  :root {
    --sea: #1f5c6a;
    --vegetation: #3f5e37;
    --forest: #24372a;
    --sand: #d9c79f;
    --paper: #fbf8f1;
    --ink: #26302b;
    --backdrop: #e9e7e4;
  }
  html, body {
    margin: 0;
    padding: 0;
    width: 1189px;
    height: 1200px;
    overflow: hidden;
    background: var(--backdrop);
  }
  .sheet {
    position: relative;
    width: 1189px;
    height: 1200px;
  }
  .card {
    position: absolute;
    left: 140px;
    width: 917px;
    height: 522px;
    box-sizing: border-box;
    overflow: hidden;
  }
  .card--front {
    top: 46px;
    background: var(--paper);
  }
  .card--back {
    top: 624px;
    background: var(--forest);
    border: 12px solid var(--sea);
  }
  .front-wave {
    position: absolute;
    inset: 0;
    width: 100%;
    height: 100%;
  }
  .brand-name {
    position: absolute;
    left: 0;
    right: 0;
    margin: 0;
    text-align: center;
    font-family: "Libre Bodoni", "Bodoni Moda", serif;
    font-weight: 700;
    font-size: 66px;
    line-height: 1;
    color: var(--paper);
    letter-spacing: 0.5px;
    white-space: nowrap;
  }
  .card--front .brand-name { top: 88px; }
  .card--back .brand-name { top: 212px; }
  .contact {
    position: absolute;
    left: 0;
    right: 0;
    top: 330px;
    margin: 0;
    text-align: center;
    font-family: "PT Sans", "Myriad Pro", sans-serif;
    font-style: normal;
    font-size: 35px;
    line-height: 45px;
    color: var(--ink);
    white-space: nowrap;
  }
  .contact span { display: block; }
</style>
</head>
<body>
<main class="sheet">
  <section class="card card--front" aria-label="Card front">
    <svg class="front-wave" viewBox="0 0 917 522" preserveAspectRatio="none" aria-hidden="true">
      <path d="M0 264 C 120 236 240 222 330 226 C 500 234 620 278 760 286 C 830 288 880 280 917 270 L 917 240 C 860 270 780 284 708 280 C 560 270 420 190 227 196 C 130 199 60 214 0 224 Z" fill="var(--sand)"/>
      <path d="M0 0 H917 V227 C 860 256 790 278 708 276 C 560 272 420 190 227 194 C 130 196 60 206 0 210 Z" fill="var(--sea)"/>
      <path d="M0 210 C 60 206 130 196 227 194 C 420 190 560 272 708 276 C 790 278 860 256 917 227" fill="none" stroke="var(--vegetation)" stroke-width="9"/>
    </svg>
    <h1 class="brand-name">Rowan Tellick Builders</h1>
    <address class="contact">
      <span class="contact-phone">021583917</span>
      <span class="contact-street">18 Kestrel Rd Harwood Bay Auckland 0814</span>
      <span class="contact-postal">PO Box 927 Mangawhai 0583</span>
    </address>
  </section>

  <section class="card card--back" aria-label="Card back">
    <p class="brand-name">Rowan Tellick Builders</p>
  </section>
</main>
</body>
</html>
```